TalbeckLabs needs a new rocket based website

We need a new website that will be based on our rocket ship logo. We develop innovative solutions for enterprises. We would like to see a design that when the pages scroll, the rocket launches and goes from launch through a journey, similar to how we approach our customer. We would like areas for "Who are we", "What can we do", "What have we done", "How can we help". http://www.talbecklabs.example.au is our current website

Target Market(s)

Government, Enterprise, Cloud

Industry/Entity Type

Software Service

Coding

Coded - Design and coding required

Number of Pages Required

2 page

Requirements
Must have
• We would like to see a design that when the pages scroll, the rocket launches and goes from launch through a journey, similar to how we approach our customer.
• Must have a home page and a detail page.
• Would like to see the logo/rocket animate in some way when you scroll through he page.

```html
<!DOCTYPE html>
<html lang="en">
<head>
<meta charset="utf-8">
<title>TalbeckLabs</title>
<link href="https://fonts.googleapis.com/css2?family=Open+Sans:wght@400;600;700&display=swap" rel="stylesheet">
<style>
:root{
  --orange:#f7931e;
  --orange-dark:#e9841a;
  --ink:#1f1f1f;
  --body:#333;
  --muted:#777;
  --page:#f3f3f2;
  --field:#ffffff;
  --line:#dcdcdc;
  --social:#1f5e9a;
}
*{box-sizing:border-box;margin:0;padding:0}
html,body{width:1200px;height:3871px;overflow:hidden}
body{position:relative;background:var(--page);font-family:"Open Sans",Arial,sans-serif;color:var(--body)}
.abs{position:absolute}
.hero{left:0;top:0;width:1200px;height:681px;background:linear-gradient(180deg,#e8b674 0%,#b8845a 25%,#4a4442 55%,#2a2d33 75%,#3c4a5a 100%)}
.brand{display:flex;align-items:center;gap:12px;font-weight:700;font-size:46px;letter-spacing:-.5px}
.brand .dot{width:26px;height:26px;border-radius:50%;background:var(--orange)}
.hero .brand{left:0;width:1200px;top:28px;justify-content:center;color:#fff}
.hero-title{left:0;width:1200px;top:365px;text-align:center;color:#fff;font-weight:700;font-size:30px;line-height:40px;text-shadow:0 2px 6px rgba(0,0,0,.4)}
.btn{background:var(--orange);color:#fff;font-size:16px;font-weight:600;display:flex;align-items:center;justify-content:center}
.hero .btn{left:524px;top:459px;width:147px;height:33px}
.section-title{font-size:30px;font-weight:600;color:var(--ink)}
.section-title span{color:var(--orange)}
.services-title{left:0;width:1200px;top:722px;text-align:center}
.service{top:816px;width:250px;text-align:center}
.service .icon{width:108px;height:108px;border-radius:50%;background:var(--orange);margin:0 auto;display:flex;align-items:center;justify-content:center}
.service h3{margin-top:30px;font-size:21px;font-weight:600;color:var(--ink)}
.service p{margin-top:10px;font-size:15px;line-height:26px;color:var(--body)}
.service .more{margin-top:6px;font-size:15px;color:var(--ink)}
.journey{left:0;top:0;width:1200px;height:3871px;pointer-events:none}
.pin{width:16px;height:16px;border-radius:50%;background:var(--orange)}
.block-title{font-size:28px}
.block-text{font-size:15px;line-height:22px;color:#222}
.art{border-radius:8px}
.ticks{list-style:none;font-size:15px;font-weight:700;color:#222}
.ticks li{display:flex;align-items:center;gap:10px;height:27px}
.ticks li::before{content:"";width:9px;height:9px;border-radius:50%;background:var(--orange)}
.field{background:var(--field);border:1px solid #eee;font-size:15px;color:#666;padding:0 16px;display:flex;align-items:center}
.map-label{font-size:30px;color:var(--ink)}
.footer-icon{width:72px;height:72px;border-radius:50%;background:var(--orange);display:flex;align-items:center;justify-content:center}
.footer-text{font-size:15px;color:#444;text-align:center;line-height:21px}
.social{width:30px;height:30px;border-radius:50%;background:var(--social)}
.rule{left:0;top:3798px;width:1200px;height:1px;background:var(--line)}
.copyright{left:0;width:1200px;top:3824px;text-align:center;font-size:15px;color:#444}
</style>
</head>
<body>

<header class="abs hero" role="img" aria-label="Photograph of a city skyline at sunset beside the waterfront">
</header>
<div class="abs brand" style="left:0;width:1200px;top:28px;justify-content:center;color:#fff"><span class="dot"></span>TalbeckLabs</div>
<h1 class="abs hero-title">Design and Development<br>of bespoke software solutions</h1>
<a class="abs btn" style="left:524px;top:459px;width:147px;height:33px">Read More</a>

<h2 class="abs section-title services-title">Our <span>Services</span></h2>

<div class="abs service" style="left:48px">
  <div class="icon"><svg width="56" height="56" viewBox="0 0 56 56" fill="none" stroke="#fff" stroke-width="3"><path d="M8 22h40L28 10z"/><path d="M12 24v18M22 24v18M34 24v18M44 24v18M6 46h44"/></svg></div>
  <h3>e-Parliament</h3>
  <p>All of your Parliamentary software and business process needs.</p>
  <div class="more">Read More.. &#8853;</div>
</div>
<div class="abs service" style="left:319px">
  <div class="icon"><svg width="60" height="44" viewBox="0 0 60 44" fill="none" stroke="#fff" stroke-width="3"><path d="M14 38h32a10 10 0 0 0 0-20 14 14 0 0 0-27-3A12 12 0 0 0 14 38z"/></svg></div>
  <h3>Cloud</h3>
  <p>Office Cloud Suite, Migration, Security, Customisations.</p>
  <div class="more">Read More.. &#8853;</div>
</div>
<div class="abs service" style="left:590px">
  <div class="icon"><svg width="56" height="56" viewBox="0 0 56 56" fill="none" stroke="#fff" stroke-width="3"><rect x="8" y="10" width="40" height="36"/><path d="M14 40l10-14 8 8 10-16M8 18h40"/></svg></div>
  <h3>Architecture &amp; Design</h3>
  <p>Business process design, technology strategy and architecture.</p>
  <div class="more">Read More.. &#8853;</div>
</div>
<div class="abs service" style="left:876px">
  <div class="icon"><svg width="56" height="56" viewBox="0 0 56 56" fill="none" stroke="#fff" stroke-width="3"><rect x="6" y="10" width="44" height="30"/><path d="M20 48h16M28 40v8M22 20l-6 5 6 5M34 20l6 5-6 5"/></svg></div>
  <h3>Software Development</h3>
  <p>Software development including business apps, web and mobile.</p>
  <div class="more">Read More.. &#8853;</div>
</div>

<svg class="abs journey" viewBox="0 0 1200 3871" aria-hidden="true">
  <path d="M560 1200 C640 1330 720 1460 675 1620 C640 1740 560 1760 555 1900 C550 2060 590 2180 600 2330 C615 2500 700 2560 690 2720 C680 2880 640 2950 640 3040" fill="none" stroke="#222" stroke-width="4" stroke-dasharray="10 9"/>
</svg>

<div class="abs art" style="left:168px;top:1251px;width:361px;height:297px;background:radial-gradient(ellipse at center,#fbd9a8 0%,#f6b45c 35%,rgba(247,147,30,.08) 75%)" role="img" aria-label="Illustration of a laptop surrounded by gears and technology icons"></div>
<div class="abs pin" style="left:694px;top:1292px"></div>
<h2 class="abs section-title block-title" style="left:748px;top:1279px">Who <span>are we</span></h2>
<p class="abs block-text" style="left:748px;top:1342px;width:340px">Lorem Ipsum is simply dummy text of the a printing and typesetting industry. Lorem Ipsum has been the industry's standard dummy text ever since the 1500s,</p>
<a class="abs btn" style="left:748px;top:1442px;width:150px;height:36px">View More</a>

<h2 class="abs section-title block-title" style="left:180px;top:1651px;width:349px;text-align:right">What <span>can we do</span></h2>
<div class="abs pin" style="left:552px;top:1664px"></div>
<p class="abs block-text" style="left:188px;top:1696px;width:340px;text-align:right">Lorem Ipsum is simply dummy text of the a printing and typesetting industry. Lorem Ipsum has been the industry's standard dummy text ever since the 1500s,</p>
<a class="abs btn" style="left:377px;top:1798px;width:147px;height:35px">View More</a>
<div class="abs art" style="left:684px;top:1496px;width:348px;height:400px;background:linear-gradient(160deg,#fbd39b 0%,#f0f0f2 45%,#e4e6f0 100%)" role="img" aria-label="Illustration of a developer working at a desk with a computer"></div>

<div class="abs art" style="left:142px;top:1974px;width:304px;height:387px;background:linear-gradient(180deg,#eceef3 0%,#2b2f66 22%,#3b3f8a 60%,#e7e8ee 100%)" role="img" aria-label="Screenshot of a completed parliament website project"></div>
<div class="abs pin" style="left:606px;top:2046px"></div>
<h2 class="abs section-title block-title" style="left:663px;top:2033px">What <span>have we done</span></h2>
<p class="abs block-text" style="left:663px;top:2093px;width:440px">Lorem Ipsum is simply dummy text of the a printing and typesetting industry. Lorem Ipsum has been the ind industry's standard dummy text ever since the 1500s,</p>
<ul class="abs ticks" style="left:663px;top:2154px">
  <li>Federal Assembly Office</li>
  <li>State Legislative Council</li>
  <li>Department of Civic Affairs</li>
</ul>
<a class="abs btn" style="left:666px;top:2258px;width:149px;height:34px">View More</a>

<div class="abs pin" style="left:668px;top:2430px"></div>
<h2 class="abs section-title" style="left:733px;top:2420px;font-size:24px">Join <span>Our Newsletter</span></h2>
<p class="abs block-text" style="left:733px;top:2476px;width:360px;font-size:14px;color:#444">Signup today for free and be the first to get notified on new updates.</p>
<div class="abs field" style="left:733px;top:2528px;width:343px;height:39px;font-size:14px">Email Here</div>
<a class="abs btn" style="left:733px;top:2588px;width:126px;height:34px;font-size:14px">Submit</a>

<div class="abs map-label" style="left:482px;top:2562px">Map</div>
<div class="abs" style="left:134px;top:2624px;width:410px;height:335px;background:linear-gradient(135deg,#eceae4 0%,#e3e6e8 50%,#dfe6dd 100%)" role="img" aria-label="Street map showing the office location"></div>

<h2 class="abs section-title" style="left:0;width:1200px;top:3078px;text-align:center;font-size:25px">Quick <span>Contact</span></h2>
<div class="abs field" style="left:232px;top:3153px;width:348px;height:41px">First Name</div>
<div class="abs field" style="left:611px;top:3153px;width:351px;height:41px">Last Name</div>
<div class="abs field" style="left:232px;top:3215px;width:348px;height:41px">Email</div>
<div class="abs field" style="left:611px;top:3215px;width:351px;height:41px">Phone</div>
<div class="abs field" style="left:232px;top:3279px;width:730px;height:152px;align-items:flex-start;padding-top:12px">How can we Help?</div>
<a class="abs btn" style="left:531px;top:3452px;width:132px;height:39px;font-weight:400">SEND</a>

<div class="abs brand" style="left:0;width:1200px;top:3518px;justify-content:center;color:var(--orange)"><span class="dot"></span>TalbeckLabs</div>

<div class="abs footer-icon" style="left:346px;top:3597px"><svg width="34" height="34" viewBox="0 0 24 24" fill="#fff"><path d="M6.6 10.8a15 15 0 0 0 6.6 6.6l2.2-2.2a1 1 0 0 1 1-.25 11.4 11.4 0 0 0 3.6.57 1 1 0 0 1 1 1V20a1 1 0 0 1-1 1A17 17 0 0 1 3 4a1 1 0 0 1 1-1h3.5a1 1 0 0 1 1 1c0 1.25.2 2.45.57 3.6a1 1 0 0 1-.25 1z"/></svg></div>
<div class="abs footer-icon" style="left:563px;top:3597px"><svg width="34" height="34" viewBox="0 0 24 24" fill="none" stroke="#fff" stroke-width="2"><path d="M3 11l9-7 9 7M5 10v10h14V10"/><rect x="10" y="14" width="4" height="6"/></svg></div>
<div class="abs footer-icon" style="left:777px;top:3597px"><svg width="34" height="34" viewBox="0 0 24 24" fill="none" stroke="#fff" stroke-width="2"><rect x="3" y="5" width="18" height="14"/><path d="M3 6l9 7 9-7"/></svg></div>
<div class="abs footer-text" style="left:282px;top:3686px;width:200px">1300 555 014</div>
<div class="abs footer-text" style="left:489px;top:3686px;width:220px">Unit 7, 48 Corran St<br>Westbury, SA 5999</div>
<div class="abs footer-text" style="left:693px;top:3686px;width:240px">info@talbecklabs.example.au</div>

<div class="abs social" style="left:520px;top:3744px"></div>
<div class="abs social" style="left:557px;top:3744px"></div>
<div class="abs social" style="left:594px;top:3744px"></div>
<div class="abs social" style="left:631px;top:3744px;background:#333"></div>

<div class="abs rule"></div>
<div class="abs copyright">Copyright © TalbeckLabs 2018. All Rights Reserved.</div>

</body>
</html>
```